UI Improvement for FlorKeep app

We are looking for a talented UI/UX designer to REFINE and enhance the visual design of our mobile application, FlorKeep. The app is fully functional, but we need a designer to improve its aesthetics by specifying design elements such as fonts, colors, spacing, and component styles.
Your task will be to analyze the CURRENT UI and provide detailed design specifications that will make the app more visually appealing, modern, and user-friendly.
TODO:
Review the existing FlorKeep app design (see attachments) and identify areas for visual improvement.
Provide a detailed UI style guide, including:
Typography (font choices, sizes, and weights)
Color palette (primary, secondary, and accent colors)
Component styling (buttons, forms, icons, and interactive elements)
Spacing and layout guidelines (margins, paddings, and alignment)
Ensure the design remains clean, modern, and professional while maintaining usability and accessibility.
Provide design mockups or visual examples (if possible) to illustrate the proposed changes.
Deliverables:
A UI Style Guide (PDF or Figma file) with specifications on fonts, colors, spacing, and UI components.
Optionally, before/after mockups or examples demonstrating the improvements.
Ideal Designer:
Strong experience in mobile UI/UX design.
Understanding of modern design trends and best practices.
Ability to communicate design choices clearly for easy developer implementation.
I have attached 7 images showcasing the main UI screens used in the FlorKeep app. These screens need visual enhancements to improve their overall look and user experience.
The images represent the current design in three key modes:
LIST Mode – Displays data in a structured list format.
READ Mode – Shows detailed information when a user selects an item.
ADD/EDIT Mode – Allows users to input or modify information.
Additionally, there is a ‘MORE’ page, which serves as a menu listing other features of the application.
Task Objective:
Please refine and improve these UIs to create a more modern, visually appealing, and user-friendly experience. Focus on typography, colors, spacing, and component styling to ensure a cohesive and polished design.
Look and feel
Each slider illustrates characteristics of the customer's brand and the style your logo design should communicate.

```html
<!DOCTYPE html>
<html lang="en">
<head>
<meta charset="utf-8">
<title>FlorKeep app – UI style guide</title>
<link rel="stylesheet" href="https://fonts.googleapis.com/css2?family=Figtree:wght@400;500;600;700&family=Nunito+Sans:wght@400;600;700;800&family=Inter:wght@400;500;600&display=swap">
<style>
:root{
  --primary:#1B7ECC;
  --ink:#1C1F34;
  --slate:#4B4B5A;
  --grey:#636669;
  --muted:#7C848B;
  --field:#F2F6F7;
  --line:#E2E7F1;
  --cyan:#25C2E3;
  --green:#29BA85;
  --orange:#F77E53;
  --yellow:#FFBE0B;
  --pink:#FF5C75;
  --violet:#7859F4;
  --black:#000;
  --white:#fff;
}
*{box-sizing:border-box;margin:0;padding:0}
html,body{width:1200px;height:929px;overflow:hidden;background:var(--white)}
.canvas{position:relative;width:1200px;height:929px;overflow:hidden}
.board{position:absolute;left:0;top:0;width:2184px;height:1702px;transform:scale(0.5495,0.5458);transform-origin:0 0;font-family:"Nunito Sans",sans-serif;color:var(--ink)}
.abs{position:absolute}
.title{left:108px;top:104px;font-family:"Figtree",sans-serif;font-weight:700;font-size:76px;letter-spacing:-1px;color:var(--black);line-height:1.2}
.section-label{font-family:"Figtree",sans-serif;font-weight:500;font-size:26px;color:var(--grey);top:302px}
.swatch{width:72px;height:72px;border-radius:6px;display:flex;align-items:center;justify-content:center;font-family:"Figtree",sans-serif;font-size:16px;color:var(--white)}
.swatch.light{color:var(--slate)}
.font-sample{left:720px;font-family:"Figtree",sans-serif;font-size:62px;color:var(--black);line-height:1.2}
.font-sample.nunito{font-family:"Nunito Sans",sans-serif}
.band{left:108px;top:721px;width:1968px;height:66px;background:var(--primary);color:var(--white);font-family:"Figtree",sans-serif;font-weight:700;font-size:27px;padding:16px 18px;line-height:34px}

/* legacy screens */
.legacy{overflow:hidden}
.statusbar{left:0;top:0;width:100%;height:44px;background:var(--black);color:var(--white);font-family:"Inter",sans-serif;font-weight:600;font-size:16px}
.navbar{left:0;top:47px;width:100%;height:50px;background:#EDEDED;box-shadow:0 4px 6px rgba(0,0,0,.08);font-family:"Inter",sans-serif}
.card{background:var(--white)}
.ofield{height:42px;border:1.5px solid var(--primary);border-radius:3px;font-family:"Inter",sans-serif;font-size:13px;color:var(--grey)}
.ofield .ph{position:absolute;left:14px;right:6px;top:12px;line-height:16px;white-space:nowrap;overflow:hidden;text-overflow:ellipsis}
.ofield .lbl{position:absolute;left:10px;top:-8px;background:var(--white);padding:0 4px;font-size:10px;font-weight:600;color:var(--primary);line-height:14px;white-space:nowrap}
.req{font-family:"Inter",sans-serif;font-size:10px;line-height:12px;color:#6FA7DA}
.tabbar{left:0;width:100%;height:56px;font-family:"Inter",sans-serif;font-size:10px;color:var(--black);display:flex}
.tabbar .tab{flex:1;display:flex;flex-direction:column;align-items:center;gap:6px;padding-top:6px}
.tabbar .tab.on{color:var(--primary)}
.homebar{height:4px;border-radius:2px;background:#555}

/* modern phones */
.phone{width:377px;height:787px;border:14px solid var(--black);border-radius:62px;background:var(--white);overflow:hidden}
.island{width:114px;height:33px;border-radius:17px;background:var(--black)}
.time{font-family:"Figtree",sans-serif;font-weight:600;font-size:17px;line-height:20px;color:var(--black)}
.h1{font-family:"Figtree",sans-serif;font-weight:700;font-size:26px;line-height:32px;color:var(--ink)}
.step{font-family:"Figtree",sans-serif;font-weight:700;font-size:15px;line-height:20px;color:var(--ink)}
.flabel{font-size:14px;line-height:18px;color:var(--ink)}
.input{background:var(--field);border-radius:6px;font-size:15px;line-height:20px;color:#B3B9BF;padding:14px 14px}
.dots{font-size:22px;color:var(--primary);letter-spacing:1px;line-height:10px}
.btn{border-radius:24px;height:48px;display:flex;align-items:center;justify-content:center;font-family:"Figtree",sans-serif;font-weight:700;font-size:16px}
.btn.primary{background:var(--primary);color:var(--white)}
.btn.ghost{border:1.5px solid var(--line);color:var(--ink)}
.divider{height:1px;background:var(--line)}
.homeline{width:120px;height:4px;border-radius:2px;background:var(--black)}

/* more list */
.menu-row{left:0;width:350px;height:37.5px;border-bottom:1px solid #DDD;font-family:"Inter",sans-serif;font-size:10px;color:var(--black);display:flex;align-items:center}
.menu-row svg{margin:0 14px 0 12px}

/* more sheet */
.tile{width:117px;text-align:center;font-size:14px;color:var(--slate);line-height:18px}
.tile .dot{width:44px;height:44px;border-radius:50%;margin:0 auto 10px;display:flex;align-items:center;justify-content:center}
.chip{font-size:10px;color:#4a4a4a;background:#8e8e8e;border-radius:8px;padding:1px 8px;line-height:14px}
</style>
</head>
<body>
<div class="canvas">
<div class="board">

  <h1 class="abs title">FlorKeep app</h1>

  <div class="abs section-label" style="left:108px">Colors</div>
  <div class="abs section-label" style="left:720px">Fonts</div>

  <div class="abs swatch" style="left:108px;top:354px;background:var(--primary)">1B7ECC</div>
  <div class="abs swatch" style="left:194px;top:354px;background:var(--ink)">1C1F34</div>
  <div class="abs swatch" style="left:280px;top:354px;background:var(--slate)">4B4B5A</div>
  <div class="abs swatch" style="left:366px;top:354px;background:var(--grey)">636669</div>
  <div class="abs swatch" style="left:452px;top:354px;background:var(--muted)">7C848B</div>
  <div class="abs swatch light" style="left:108px;top:447px;background:var(--field)">F2F6F7</div>
  <div class="abs swatch light" style="left:194px;top:447px;background:var(--line)">E2E7F1</div>
  <div class="abs swatch" style="left:108px;top:541px;background:var(--cyan)">25C2E3</div>
  <div class="abs swatch" style="left:194px;top:541px;background:var(--green)">29BA85</div>
  <div class="abs swatch" style="left:280px;top:541px;background:var(--orange)">F77E53</div>
  <div class="abs swatch" style="left:366px;top:541px;background:var(--yellow)">FFBE0B</div>
  <div class="abs swatch" style="left:452px;top:541px;background:var(--pink)">FF5C75</div>
  <div class="abs swatch" style="left:538px;top:541px;background:var(--violet)">7859F4</div>

  <div class="abs font-sample" style="top:350px">Figtree</div>
  <div class="abs font-sample nunito" style="top:444px">Nunito Sans</div>

  <div class="abs band">Add-Edit Page &amp; More page</div>

  <!-- Screen: legacy add contact -->
  <section class="abs legacy" style="left:108px;top:823px;width:350px;height:757px;background:#F3F3F3">
    <div class="abs statusbar"><span class="abs" style="left:46px;top:14px">10:37</span>
      <svg class="abs" style="left:248px;top:15px" width="74" height="14"><circle cx="3" cy="11" r="1.2" fill="#fff"/><circle cx="8" cy="11" r="1.2" fill="#fff"/><circle cx="13" cy="11" r="1.2" fill="#fff"/><circle cx="18" cy="11" r="1.2" fill="#fff"/><path d="M26 5a11 11 0 0 1 14 0M29 8a6 6 0 0 1 8 0" stroke="#fff" stroke-width="2" fill="none"/><circle cx="33" cy="11" r="1.6" fill="#fff"/><rect x="48" y="2" width="22" height="10" rx="3" fill="#fff"/></svg>
    </div>
    <div class="abs navbar">
      <svg class="abs" style="left:16px;top:16px" width="16" height="14"><path d="M15 7H2M7 1L1 7l6 6" stroke="#000" stroke-width="2" fill="none"/></svg>
      <div class="abs" style="left:0;width:350px;text-align:center;top:8px;font-size:9px;line-height:11px;color:#666">Add</div>
      <div class="abs" style="left:0;width:350px;text-align:center;top:20px;font-size:14px;line-height:17px">Contact</div>
      <div class="abs" style="left:278px;top:14px;font-size:14px;line-height:17px;color:var(--primary)">Save</div>
      <div class="abs" style="left:318px;top:8px;font-size:16px;font-weight:700">···</div>
    </div>
    <div class="abs card" style="left:6px;top:104px;width:338px;height:298px">
      <div class="abs ofield" style="left:8px;top:16px;width:291px"><span class="lbl">Business Name -e</span><span class="ph">enter contactbusinessname -e</span></div>
      <div class="abs" style="left:316px;top:28px;font-weight:700">···</div>
      <div class="abs ofield" style="left:8px;top:81px;width:322px"><span class="lbl">First Name -e</span><span class="ph">enter contactfirstname -e</span></div>
      <div class="abs ofield" style="left:8px;top:146px;width:322px"><span class="lbl">Middle Name -e</span><span class="ph">enter contactmiddlename -e</span></div>
      <div class="abs ofield" style="left:8px;top:211px;width:322px"><span class="lbl">Last Name -e</span><span class="ph">enter contactlastname -e</span></div>
      <div class="abs" style="left:8px;top:285px;width:322px;height:2px;background:#DDD"></div>
    </div>
    <div class="abs card" style="left:6px;top:410px;width:338px;height:280px">
      <svg class="abs" style="left:318px;top:14px" width="14" height="8"><path d="M1 7l6-6 6 6" stroke="#999" fill="none" stroke-width="1.5"/></svg>
      <div class="abs ofield" style="left:8px;top:34px;width:291px"><span class="lbl">AddressLabelTag -e</span>
        <svg class="abs" style="left:272px;top:15px" width="14" height="9"><path d="M0 0h14L7 8z" fill="#6FA7DA"/></svg></div>
      <div class="abs" style="left:316px;top:46px;font-weight:700">···</div>
      <div class="abs req" style="left:22px;top:80px">Required</div>
      <div class="abs ofield" style="left:8px;top:99px;width:322px"><span class="lbl">AddressLine1 -e</span><span class="ph">enter addressline1 -e</span></div>
      <div class="abs req" style="left:22px;top:145px">Required</div>
      <div class="abs ofield" style="left:8px;top:164px;width:322px"><span class="lbl">AddressLine2 -e</span><span class="ph">enter addressline2 -e</span></div>
      <div class="abs ofield" style="left:8px;top:229px;width:91px"><span class="lbl">AddressCity</span><span class="ph">enter addr...</span></div>
      <div class="abs ofield" style="left:108px;top:229px;width:91px"><span class="lbl">AddressState</span>
        <svg class="abs" style="left:72px;top:15px" width="14" height="9"><path d="M0 0h14L7 8z" fill="#6FA7DA"/></svg></div>
      <div class="abs ofield" style="left:208px;top:229px;width:91px"><span class="lbl">Zip -e</span><span class="ph">enter addr...</span></div>
    </div>
    <nav class="abs tabbar" style="top:690px;background:var(--white)">
      <div class="tab on"><svg width="12" height="12"><circle cx="6" cy="3.5" r="3" fill="currentColor"/><path d="M0 12a6 5 0 0 1 12 0z" fill="currentColor"/></svg>Contact</div>
      <div class="tab"><svg width="12" height="12"><circle cx="6" cy="6" r="5" fill="currentColor"/></svg>Quote</div>
      <div class="tab"><svg width="12" height="12"><rect x="0" y="3" width="12" height="9" rx="1.5" fill="currentColor"/><rect x="4" y="0" width="4" height="4" fill="none" stroke="currentColor"/></svg>WorkOrder</div>
      <div class="tab"><svg width="12" height="12"><circle cx="6" cy="6" r="5" fill="currentColor"/></svg>Invoice</div>
      <div class="tab"><span style="font-weight:700;line-height:12px">···</span>More</div>
    </nav>
    <div class="abs homebar" style="left:112px;top:749px;width:126px"></div>
  </section>

  <!-- Screen: add contact step 1 -->
  <section class="abs phone" style="left:481px;top:808px">
    <div class="abs time" style="left:32px;top:30px">9:41</div>
    <div class="abs island" style="left:118px;top:11px"></div>
    <svg class="abs" style="left:255px;top:34px" width="80" height="12"><rect x="0" y="8" width="3" height="4" fill="#000"/><rect x="5" y="6" width="3" height="6" fill="#000"/><rect x="10" y="3" width="3" height="9" fill="#000"/><rect x="15" y="0" width="3" height="12" fill="#000"/><path d="M26 5a9 9 0 0 1 12 0M29 8a5 5 0 0 1 6 0" stroke="#000" stroke-width="2" fill="none"/><circle cx="32" cy="11" r="1.3" fill="#000"/><rect x="52" y="1" width="22" height="10" rx="3" fill="#000"/></svg>
    <svg class="abs" style="left:14px;top:78px" width="20" height="16"><path d="M19 8H2M8 1L1 8l7 7" stroke="var(--primary)" stroke-width="1.8" fill="none"/></svg>
    <div class="abs h1" style="left:53px;top:70px">Add Contact</div>
    <div class="abs dots" style="left:315px;top:80px">···</div>
    <div class="abs step" style="left:13px;top:126px">1 / 2 : Contact Name</div>
    <div class="abs dots" style="left:315px;top:134px">···</div>
    <div class="abs flabel" style="left:13px;top:163px">Business Name</div>
    <div class="abs input" style="left:13px;top:187px;width:321px;height:48px">Enter</div>
    <div class="abs flabel" style="left:13px;top:249px">First Name</div>
    <div class="abs input" style="left:13px;top:273px;width:321px;height:48px">Enter</div>
    <div class="abs flabel" style="left:13px;top:335px">Middle Name</div>
    <div class="abs input" style="left:13px;top:359px;width:321px;height:48px">Enter</div>
    <div class="abs flabel" style="left:13px;top:421px">Last Name</div>
    <div class="abs input" style="left:13px;top:445px;width:321px;height:48px">Enter</div>
    <div class="abs divider" style="left:0;top:513px;width:349px"></div>
    <div class="abs btn primary" style="left:13px;top:531px;width:321px">Next</div>
    <div class="abs homeline" style="left:114px;top:749px"></div>
  </section>

  <!-- Screen: add contact step 2 -->
  <section class="abs phone" style="left:866px;top:808px">
    <div class="abs time" style="left:32px;top:30px">9:41</div>
    <div class="abs island" style="left:119px;top:11px"></div>
    <svg class="abs" style="left:255px;top:34px" width="80" height="12"><rect x="0" y="8" width="3" height="4" fill="#000"/><rect x="5" y="6" width="3" height="6" fill="#000"/><rect x="10" y="3" width="3" height="9" fill="#000"/><rect x="15" y="0" width="3" height="12" fill="#000"/><path d="M26 5a9 9 0 0 1 12 0M29 8a5 5 0 0 1 6 0" stroke="#000" stroke-width="2" fill="none"/><circle cx="32" cy="11" r="1.3" fill="#000"/><rect x="52" y="1" width="22" height="10" rx="3" fill="#000"/></svg>
    <svg class="abs" style="left:14px;top:78px" width="20" height="16"><path d="M19 8H2M8 1L1 8l7 7" stroke="var(--primary)" stroke-width="1.8" fill="none"/></svg>
    <div class="abs h1" style="left:54px;top:70px">Add Contact</div>
    <div class="abs dots" style="left:316px;top:80px">···</div>
    <div class="abs step" style="left:14px;top:126px">2 / 2 : Contact Address</div>
    <div class="abs dots" style="left:316px;top:134px">···</div>
    <div class="abs flabel" style="left:14px;top:163px">Address Label Tag</div>
    <div class="abs input" style="left:14px;top:187px;width:321px;height:48px">Select
      <svg class="abs" style="left:292px;top:20px" width="12" height="8"><path d="M1 1l5 5 5-5" stroke="var(--primary)" stroke-width="1.5" fill="none"/></svg></div>
    <div class="abs flabel" style="left:14px;top:249px">Address Line 1</div>
    <div class="abs input" style="left:14px;top:273px;width:321px;height:68px">Enter</div>
    <div class="abs flabel" style="left:14px;top:355px">Address Line 2</div>
    <div class="abs input" style="left:14px;top:379px;width:321px;height:68px">Enter</div>
    <div class="abs flabel" style="left:14px;top:461px">City</div>
    <div class="abs input" style="left:14px;top:485px;width:321px;height:48px">Enter</div>
    <div class="abs flabel" style="left:14px;top:547px">State</div>
    <div class="abs flabel" style="left:182px;top:547px">ZIP</div>
    <div class="abs input" style="left:14px;top:571px;width:153px;height:48px">Select
      <svg class="abs" style="left:124px;top:20px" width="12" height="8"><path d="M1 1l5 5 5-5" stroke="var(--primary)" stroke-width="1.5" fill="none"/></svg></div>
    <div class="abs input" style="left:182px;top:571px;width:153px;height:48px">Enter</div>
    <div class="abs divider" style="left:0;top:638px;width:349px"></div>
    <div class="abs btn ghost" style="left:14px;top:657px;width:153px">Back</div>
    <div class="abs btn primary" style="left:182px;top:657px;width:153px">Save</div>
    <div class="abs homeline" style="left:116px;top:740px"></div>
  </section>

  <!-- Screen: legacy more menu -->
  <section class="abs legacy" style="left:1339px;top:823px;width:350px;height:757px;background:var(--white)">
    <div class="abs statusbar"><span class="abs" style="left:51px;top:14px">3:01</span>
      <svg class="abs" style="left:248px;top:15px" width="74" height="14"><circle cx="3" cy="11" r="1.2" fill="#fff"/><circle cx="8" cy="11" r="1.2" fill="#fff"/><circle cx="13" cy="11" r="1.2" fill="#fff"/><circle cx="18" cy="11" r="1.2" fill="#fff"/><path d="M26 5a11 11 0 0 1 14 0M29 8a6 6 0 0 1 8 0" stroke="#fff" stroke-width="2" fill="none"/><circle cx="33" cy="11" r="1.6" fill="#fff"/><rect x="48" y="2" width="22" height="10" rx="3" fill="#fff"/></svg>
    </div>
    <div class="abs navbar">
      <div class="abs" style="left:0;width:350px;text-align:center;top:14px;font-size:15px;line-height:18px;color:#333">More</div>
      <div class="abs" style="left:318px;top:8px;font-size:16px;font-weight:700">···</div>
    </div>
    <div class="abs menu-row" style="top:97px"><svg width="14" height="12"><path d="M0 10h14M1 6l11-4 1 2-9 4z" stroke="#000" stroke-width="1.6" fill="#000"/></svg>Flight</div>
    <div class="abs menu-row" style="top:134.5px"><svg width="14" height="12"><circle cx="4" cy="2.5" r="2.2" fill="#000"/><circle cx="10" cy="2.5" r="2.2" fill="#000"/><rect x="2" y="5" width="4" height="7" fill="#000"/><rect x="8" y="5" width="4" height="7" fill="#000"/></svg>Login</div>
    <div class="abs menu-row" style="top:172px"><svg width="14" height="12"><circle cx="7" cy="3" r="3" fill="#000"/><path d="M1 12a6 5 0 0 1 12 0z" fill="#000"/></svg>Account</div>
    <div class="abs menu-row" style="top:209.5px"><svg width="14" height="12"><rect x="2" y="1" width="10" height="11" rx="1.5" fill="#000"/></svg>Calendar</div>
    <div class="abs menu-row" style="top:247px"><svg width="14" height="12"><circle cx="4" cy="3" r="2" fill="#000"/><circle cx="10" cy="3" r="2" fill="#000"/><path d="M0 11a4 4 0 0 1 8 0zM6 11a4 4 0 0 1 8 0z" fill="#000"/></svg>Users</div>
    <div class="abs menu-row" style="top:284.5px"><svg width="14" height="12"><path d="M7 0l7 6h-2v6H9V8H5v4H2V6H0z" fill="#000"/></svg>Dashboard</div>
    <div class="abs menu-row" style="top:322px"><svg width="14" height="12"><path d="M0 2l4-1 5 2 5-1v9l-5 1-5-2-4 1z" fill="#000"/></svg>Tracking</div>
    <div class="abs menu-row" style="top:359.5px"><svg width="14" height="12"><rect x="1" y="4" width="12" height="8" fill="#000"/><rect x="0" y="2" width="14" height="3" fill="#000"/></svg>Outreach Event</div>
    <div class="abs menu-row" style="top:397px"><svg width="14" height="12"><path d="M1 11L9 3" stroke="#000" stroke-width="2.5"/><circle cx="11" cy="2" r="2" fill="#000"/></svg>Maintenance Resource</div>
    <div class="abs menu-row" style="top:434.5px"><svg width="14" height="12"><circle cx="7" cy="6" r="5" fill="none" stroke="#000" stroke-width="3" stroke-dasharray="2.5 1.4"/><circle cx="7" cy="6" r="2.5" fill="#000"/></svg>Setting</div>
    <nav class="abs tabbar" style="top:690px;background:var(--white);border-top:1px solid #DDD">
      <div class="tab"><svg width="12" height="12"><circle cx="6" cy="3.5" r="3" fill="currentColor"/><path d="M0 12a6 5 0 0 1 12 0z" fill="currentColor"/></svg>Contact</div>
      <div class="tab"><svg width="12" height="12"><circle cx="6" cy="4" r="3" fill="currentColor"/><rect x="2" y="8" width="8" height="4" fill="currentColor"/></svg>Pilot</div>
      <div class="tab"><svg width="12" height="12"><path d="M6 0v12M0 6h12M3 11h6" stroke="currentColor" stroke-width="2"/></svg>Plane</div>
      <div class="tab"><svg width="12" height="12"><path d="M4 0v7l-2 1 4 4h5V6z" fill="currentColor"/></svg>Flt Request</div>
      <div class="tab on"><span style="font-weight:700;line-height:12px">···</span>More</div>
    </nav>
    <div class="abs homebar" style="left:113px;top:749px;width:126px"></div>
  </section>

  <!-- Screen: modern more sheet -->
  <section class="abs phone" style="left:1712px;top:808px;background:#7E7E7E">
    <div class="abs time" style="left:32px;top:30px;color:#2a2a2a">9:41</div>
    <div class="abs island" style="left:118px;top:11px"></div>
    <svg class="abs" style="left:255px;top:34px" width="80" height="12"><rect x="0" y="8" width="3" height="4" fill="#000"/><rect x="5" y="6" width="3" height="6" fill="#000"/><rect x="10" y="3" width="3" height="9" fill="#000"/><rect x="15" y="0" width="3" height="12" fill="#000"/><path d="M26 5a9 9 0 0 1 12 0M29 8a5 5 0 0 1 6 0" stroke="#000" stroke-width="2" fill="none"/><circle cx="32" cy="11" r="1.3" fill="#000"/><rect x="52" y="1" width="22" height="10" rx="3" fill="#000"/></svg>
    <div class="abs h1" style="left:14px;top:70px;color:#1a1a1a">Contact</div>
    <svg class="abs" style="left:272px;top:80px" width="18" height="18"><path d="M9 0v18M0 9h18" stroke="#124f80" stroke-width="2"/></svg>
    <div class="abs dots" style="left:316px;top:80px;color:#124f80">···</div>
    <div class="abs" style="left:15px;top:108px;width:320px;height:40px;border-radius:20px;background:#747474">
      <svg class="abs" style="left:14px;top:11px" width="18" height="18"><circle cx="7.5" cy="7.5" r="6" stroke="#444" stroke-width="1.6" fill="none"/><path d="M12 12l5 5" stroke="#444" stroke-width="1.6"/></svg>
      <span class="abs" style="left:42px;top:10px;font-size:15px;line-height:20px;color:#4a4a4a">Search</span>
      <svg class="abs" style="left:286px;top:12px" width="20" height="16"><path d="M0 4h20M0 12h20" stroke="#4a4a4a" stroke-width="1.4"/><circle cx="6" cy="4" r="2.6" fill="#747474" stroke="#4a4a4a" stroke-width="1.4"/><circle cx="14" cy="12" r="2.6" fill="#747474" stroke="#4a4a4a" stroke-width="1.4"/></svg>
    </div>
    <div class="abs" style="left:14px;top:178px;width:44px;height:44px;border-radius:50%;background:#1c5b44;color:#0f3a2b;font-size:13px;display:flex;align-items:center;justify-content:center">AC</div>
    <div class="abs" style="left:73px;top:178px;font-size:18px;line-height:22px;color:#1a1a1a">Ashford, Colin</div>
    <div class="abs" style="left:73px;top:205px;display:flex;gap:8px"><span class="chip">Aircraft Owner</span><span class="chip">Enthusiast</span><span class="chip">Flight Support</span></div>
    <div class="abs" style="left:14px;top:250px;width:44px;height:44px;border-radius:50%;background:#144b7a"></div>
    <div class="abs" style="left:73px;top:252px;font-size:18px;line-height:22px;color:#1a1a1a">Arden, Miles Grant</div>

    <div class="abs" style="left:0;top:265px;width:349px;height:520px;background:var(--white);border-radius:24px 24px 0 0">
      <div class="abs tile" style="left:13px;top:28px"><div class="dot" style="background:var(--cyan)"><svg width="20" height="16"><path d="M1 14h18M2 9l14-5 2 2-12 5z" stroke="#fff" stroke-width="1.5" fill="none" stroke-linejoin="round"/></svg></div>Flight</div>
      <div class="abs tile" style="left:130px;top:28px"><div class="dot" style="background:var(--green)"><svg width="20" height="20"><path d="M8 2h9v16H8M2 10h10M8 6l4 4-4 4" stroke="#fff" stroke-width="1.6" fill="none"/></svg></div>Login</div>
      <div class="abs tile" style="left:247px;top:28px"><div class="dot" style="background:var(--orange)"><svg width="20" height="20"><circle cx="10" cy="10" r="8" stroke="#fff" stroke-width="1.6" fill="none"/><circle cx="10" cy="8" r="3" stroke="#fff" stroke-width="1.6" fill="none"/><path d="M5 16a6 5 0 0 1 10 0" stroke="#fff" stroke-width="1.6" fill="none"/></svg></div>Account</div>
      <div class="abs tile" style="left:13px;top:125px"><div class="dot" style="background:var(--yellow)"><svg width="20" height="20"><rect x="2" y="4" width="16" height="14" rx="2" stroke="#fff" stroke-width="1.6" fill="none"/><path d="M2 8h16M6 2v4M14 2v4" stroke="#fff" stroke-width="1.6"/></svg></div>Calendar</div>
      <div class="abs tile" style="left:130px;top:125px"><div class="dot" style="background:var(--pink)"><svg width="20" height="20"><circle cx="7" cy="7" r="3" stroke="#fff" stroke-width="1.6" fill="none"/><circle cx="14" cy="7" r="3" stroke="#fff" stroke-width="1.6" fill="none"/><path d="M2 17a5 5 0 0 1 10 0M9 17a5 5 0 0 1 10 0" stroke="#fff" stroke-width="1.6" fill="none"/></svg></div>Users</div>
      <div class="abs tile" style="left:247px;top:125px"><div class="dot" style="background:var(--violet)"><svg width="20" height="20"><path d="M3 9l7-6 7 6v9H3z" stroke="#fff" stroke-width="1.6" fill="none" stroke-linejoin="round"/><path d="M8 18v-5h4v5" stroke="#fff" stroke-width="1.6" fill="none"/></svg></div>Dashboard</div>
      <div class="abs tile" style="left:13px;top:222px"><div class="dot" style="background:var(--cyan)"><svg width="20" height="20"><path d="M2 5l5-2 6 2 5-2v12l-5 2-6-2-5 2z" stroke="#fff" stroke-width="1.6" fill="none" stroke-linejoin="round"/><path d="M7 3v12M13 5v12" stroke="#fff" stroke-width="1.6"/></svg></div>Tracking</div>
      <div class="abs tile" style="left:130px;top:222px"><div class="dot" style="background:var(--green)"><svg width="20" height="20"><rect x="2" y="6" width="16" height="4" stroke="#fff" stroke-width="1.6" fill="none"/><rect x="4" y="10" width="12" height="8" stroke="#fff" stroke-width="1.6" fill="none"/><path d="M10 6v12" stroke="#fff" stroke-width="1.6"/></svg></div>Outreach<br>Event</div>
      <div class="abs tile" style="left:247px;top:222px"><div class="dot" style="background:var(--orange)"><svg width="20" height="20"><path d="M3 17l8-8" stroke="#fff" stroke-width="2"/><circle cx="13" cy="7" r="4" stroke="#fff" stroke-width="1.6" fill="none"/></svg></div>Maintenance<br>Resource</div>
      <div class="abs tile" style="left:13px;top:319px"><div class="dot" style="background:var(--yellow)"><svg width="20" height="20"><circle cx="10" cy="10" r="7" stroke="#fff" stroke-width="2.5" fill="none" stroke-dasharray="3 2"/><circle cx="10" cy="10" r="3" stroke="#fff" stroke-width="1.6" fill="none"/></svg></div>Setting</div>

      <nav class="abs" style="left:0;top:418px;width:349px;height:56px;display:flex;border-top:1px solid var(--line);font-size:9px;line-height:12px;color:var(--muted)">
        <div style="flex:1;text-align:center;padding-top:8px"><svg width="18" height="18"><rect x="3" y="1" width="12" height="16" rx="2" stroke="#7C848B" fill="none" stroke-width="1.3"/><circle cx="9" cy="7" r="2.5" stroke="#7C848B" fill="none" stroke-width="1.3"/><path d="M5 14a4 3 0 0 1 8 0" stroke="#7C848B" fill="none" stroke-width="1.3"/></svg><br>Contact</div>
        <div style="flex:1;text-align:center;padding-top:8px"><svg width="18" height="18"><circle cx="9" cy="6" r="4" stroke="#7C848B" fill="none" stroke-width="1.3"/><path d="M3 17a6 5 0 0 1 12 0z" stroke="#7C848B" fill="none" stroke-width="1.3"/></svg><br>Pilot</div>
        <div style="flex:1;text-align:center;padding-top:8px"><svg width="18" height="18"><path d="M9 1v16M1 9h16M5 16h8" stroke="#7C848B" fill="none" stroke-width="1.3"/></svg><br>Plane</div>
        <div style="flex:1;text-align:center;padding-top:8px"><svg width="18" height="18"><path d="M7 2v9l-3-2-1 2 5 5h7V9l-6-2V2z" stroke="#7C848B" fill="none" stroke-width="1.3" stroke-linejoin="round"/></svg><br>Flt Request</div>
        <div style="flex:1;text-align:center;padding-top:8px;color:var(--primary);font-weight:700"><svg width="18" height="18"><path d="M2 4h14M2 9h14M2 14h14" stroke="#1B7ECC" stroke-width="1.6"/></svg><br>More</div>
      </nav>
      <div class="abs homeline" style="left:114px;top:484px"></div>
    </div>
  </section>

</div>
</div>
</body>
</html>
```